One of a Kind Clean Business Card

We need to design a new business card template for our company. Our company designs and produced merchandising displays. You can see a sample of what we produce on our site www.qorvanexhibits.net. I have uploaded our logo in vector format, as well as a picture of our current business cards. We want a totally different look. We want simple and clean, looking forward to seeing what people create.
Updates

I would like to update the address for Qorvan Display Group Inc. 518 E Tollmere Ln Arlington Heights, IL 60017 Would also note. No QR codes

Industry/Entity Type

Business

Contact Information for Business Card

Need a 1 sided business card designed.

Font styles to use
Serif

Requirements
Must have
• Easy to view; Clean Design
Nice to have
• Features that promote engineering and creativity
Should not have
• Too much clutter, keep it simple

```html
<!DOCTYPE html>
<html lang="en">
<head>
<meta charset="utf-8">
<title>Qorvan Display Group Inc. — Business Card</title>
<link rel="stylesheet" href="https://fonts.googleapis.com/css2?family=Open+Sans:wght@400;600&display=swap">
<style>
  :root {
    --stage: #e9e7e5;
    --card-white: #ffffff;
    --card-black: #000000;
    --brand-red: #8f0e16;
    --name-red: #b3131c;
    --text-light: #d9d9d9;
    --icon-red: #b01a22;
    --white: #ffffff;
  }
  * { box-sizing: border-box; margin: 0; padding: 0; }
  html, body {
    width: 1200px; height: 900px; overflow: hidden;
    background: var(--stage);
    font-family: "Open Sans", Arial, sans-serif;
  }
  .canvas { position: relative; width: 1200px; height: 900px; }

  .card { position: absolute; overflow: hidden; box-shadow: 0 4px 14px rgba(0,0,0,.18); }

  /* Front */
  .card-front { left: 78px; top: 34px; width: 588px; height: 364px; background: var(--card-white); }
  .front-bands { position: absolute; left: 0; top: 0; width: 588px; height: 364px; }
  .front-wordmark {
    position: absolute; left: 0; top: 128px; width: 588px; text-align: center;
    color: var(--brand-red); font-size: 24px; font-weight: 400; letter-spacing: .5px;
  }
  .contact-list { position: absolute; left: 28px; top: 256px; list-style: none; }
  .contact-list li {
    display: flex; align-items: center; gap: 8px;
    color: var(--text-light); font-size: 15px; line-height: 21.5px;
  }
  .contact-list svg { width: 12px; height: 12px; flex: none; }
  .holder { position: absolute; right: 37px; top: 254px; text-align: right; }
  .holder-name { color: var(--name-red); font-size: 20px; font-weight: 400; letter-spacing: .3px; }
  .holder-address { color: var(--text-light); font-size: 15px; line-height: 21.5px; margin-top: 8px; }

  /* Back */
  .card-back { left: 388px; top: 505px; width: 567px; height: 352px; background: var(--brand-red); }
  .back-wordmark {
    position: absolute; left: 0; top: 166px; width: 567px; text-align: center;
    color: var(--white); font-size: 24px; font-weight: 400; letter-spacing: .5px;
  }
  .back-url {
    position: absolute; left: 0; top: 292px; width: 567px; text-align: center;
    color: var(--white); font-size: 14px; font-weight: 600;
  }
</style>
</head>
<body>
<main class="canvas">

  <section class="card card-front" aria-label="Card front">
    <svg class="front-bands" viewBox="0 0 588 364" aria-hidden="true">
      <polygon points="0,189 398,189 378,215 0,215" fill="var(--brand-red)"/>
      <polygon points="0,218 384,218 414,180 588,180 588,364 0,364" fill="var(--card-black)"/>
    </svg>
    <p class="front-wordmark">Qorvan Display Group Inc.</p>

    <ul class="contact-list">
      <li>
        <svg viewBox="0 0 12 12"><path d="M1 4 Q6 0 11 4 L9 5.5 7.5 4 4.5 4 3 5.5Z M2.5 6 H9.5 L10.5 11 H1.5Z" fill="var(--icon-red)"/></svg>
        847-555-0142
      </li>
      <li>
        <svg viewBox="0 0 12 12"><rect x="3" y="0.5" width="6" height="11" rx="1" fill="none" stroke="var(--icon-red)" stroke-width="1.3"/><circle cx="6" cy="9.5" r=".8" fill="var(--icon-red)"/></svg>
        312-555-0176
      </li>
      <li>
        <svg viewBox="0 0 12 12"><rect x="0.5" y="2.5" width="11" height="7.5" fill="var(--icon-red)"/><path d="M0.5 2.5 L6 7 L11.5 2.5" fill="none" stroke="var(--card-black)" stroke-width=".9"/></svg>
        dferrow@qorvanexhibits.net
      </li>
      <li>
        <svg viewBox="0 0 12 12"><circle cx="6" cy="6" r="5.3" fill="var(--icon-red)"/><path d="M0.7 6 H11.3 M6 0.7 Q3 6 6 11.3 M6 0.7 Q9 6 6 11.3" fill="none" stroke="var(--card-black)" stroke-width=".8"/></svg>
        www.qorvanexhibits.net
      </li>
    </ul>

    <div class="holder">
      <p class="holder-name">DANA FERROW</p>
      <p class="holder-address">518 E Tollmere Ln<br>Arlington Heights, IL 60017</p>
    </div>
  </section>

  <section class="card card-back" aria-label="Card back">
    <p class="back-wordmark">Qorvan Display Group Inc.</p>
    <p class="back-url">www.qorvanexhibits.net</p>
  </section>

</main>
</body>
</html>
```